Website images and banners needed to be created

We have a website we have not used in a few months that need updated sales banners and images resized for our web devs to upload and update. The site in question is w w w . p a l t r o n . c o m

Number of Pages Required

3 page

```html
<!DOCTYPE html>
<html lang="en">
<head>
<meta charset="utf-8">
<title>Big Black Friday Event Banners</title>
<link href="https://fonts.googleapis.com/css2?family=Great+Vibes&family=Lato:ital,wght@0,400;0,700;0,900;1,700;1,900&display=swap" rel="stylesheet">
<style>
  :root{
    --stage:#2378cf;
    --paper:#f4f4f4;
    --orange:#f36a10;
    --brown:#5a3716;
    --brown-dark:#2e1b09;
    --slate:#4a4a4c;
    --black:#000000;
    --white:#ffffff;
    --frame:#cfcfcf;
  }
  *{margin:0;padding:0;box-sizing:border-box}
  html,body{width:1200px;height:818px;overflow:hidden;background:var(--stage)}
  .canvas{position:relative;width:1200px;height:818px;background:var(--stage)}
  .banner{position:absolute;left:55px;width:1091px;height:349px;overflow:hidden;font-family:"Lato",sans-serif}
  .banner--light{top:44px;background:var(--paper)}
  .banner--dark{top:415px;background:var(--black)}
  .banner__art{position:absolute;inset:0;width:100%;height:100%}
  .line{position:absolute;white-space:nowrap;line-height:1}
  .script{font-family:"Great Vibes",cursive;font-size:31px;color:var(--black)}
  .headline{font-weight:700;color:var(--orange);font-size:56px}
  .event{font-weight:700;color:var(--slate);font-size:81px;letter-spacing:-1px}
  .tagline{font-weight:700;color:var(--orange);font-size:26px;letter-spacing:-1px}
  .title-block{position:absolute;width:400px;height:100%;top:0;text-align:center}
  .title-block .line{left:0;right:0}
  .discount-upto{font-weight:900;color:var(--orange);font-size:19px}
  .discount-figure{font-weight:900;color:var(--brown);font-size:116px;letter-spacing:-3px;
    text-shadow:1px 1px 0 var(--brown-dark),2px 2px 0 var(--brown-dark),3px 3px 0 var(--brown-dark),4px 4px 2px rgba(0,0,0,.25)}
  .discount-label{font-weight:700;color:var(--orange);font-size:27px}
  .size-tag{position:absolute;right:8px;bottom:9px;font-size:10px;font-weight:700;color:var(--black)}
  .banner--dark .size-tag{color:var(--white)}
  .banner--dark .script{color:var(--white)}
  .banner--dark .event{color:var(--white)}
  .promo-upto{font-weight:900;font-style:italic;color:var(--orange);font-size:18px}
  .promo-figure{font-weight:900;color:var(--brown);font-size:86px;letter-spacing:-2px;transform:scaleX(.82);transform-origin:left top;
    text-shadow:1px 1px 0 var(--brown-dark),2px 2px 0 var(--brown-dark),3px 3px 1px rgba(0,0,0,.3)}
  .promo-label{font-weight:900;font-style:italic;color:var(--orange);font-size:34px;letter-spacing:-1px}
</style>
</head>
<body>
<main class="canvas">

  <section class="banner banner--light" aria-label="Black Friday banner, light version">
    <svg class="banner__art" viewBox="0 0 1500 480" preserveAspectRatio="none">
      <defs>
        <linearGradient id="roomSketch" x1="0" y1="0" x2="1" y2="1">
          <stop offset="0" stop-color="#f6f6f6"/>
          <stop offset=".5" stop-color="#eceded"/>
          <stop offset="1" stop-color="#e2e3e3"/>
        </linearGradient>
        <linearGradient id="photoTop" x1="0" y1="0" x2="0" y2="1">
          <stop offset="0" stop-color="#3a2f26"/>
          <stop offset=".35" stop-color="#d9d4c8"/>
          <stop offset=".6" stop-color="#eeeeec"/>
          <stop offset="1" stop-color="#b9b2a8"/>
        </linearGradient>
        <linearGradient id="photoBottom" x1="0" y1="0" x2="0" y2="1">
          <stop offset="0" stop-color="#9a9c9c"/>
          <stop offset=".4" stop-color="#e3d5d3"/>
          <stop offset=".7" stop-color="#55585b"/>
          <stop offset="1" stop-color="#c7c8c4"/>
        </linearGradient>
        <linearGradient id="photoCentre" x1="0" y1="0" x2="0" y2="1">
          <stop offset="0" stop-color="#dcd8ce"/>
          <stop offset=".45" stop-color="#b3aa9c"/>
          <stop offset=".75" stop-color="#8e887d"/>
          <stop offset="1" stop-color="#4c5548"/>
        </linearGradient>
      </defs>
      <rect x="700" y="0" width="800" height="480" fill="url(#roomSketch)" role="img" aria-label="Faint line sketch of a bedroom interior"/>
      <polygon points="355,90 403,-5 635,-5 683,90 635,233 410,233" fill="url(#photoTop)" stroke="var(--frame)" stroke-width="4" role="img" aria-label="Photo of a white mattress on a cream upholstered bed"/>
      <polygon points="355,390 410,245 630,245 683,390 630,485 410,485" fill="url(#photoBottom)" stroke="var(--frame)" stroke-width="4" role="img" aria-label="Photo of a white metal bed with cushions"/>
      <polygon points="610,240 722,45 945,45 1058,240 945,435 722,435" fill="url(#photoCentre)" stroke="var(--frame)" stroke-width="4" role="img" aria-label="Photo of a bedroom with a grey tufted bed and curtains"/>
    </svg>

    <p class="line discount-upto" style="left:25px;top:107px">UPTO</p>
    <p class="line discount-figure" style="left:23px;top:109px">70%</p>
    <p class="line discount-label" style="left:31px;top:213px">OFF EVERTHING</p>

    <div class="title-block" style="left:731px">
      <p class="line script" style="top:88px">The Big Black</p>
      <p class="line headline" style="top:119px">FRIDAY</p>
      <p class="line event" style="top:160px">EVENT</p>
      <p class="line tagline" style="top:230px">SALE MUST END SOON</p>
    </div>
    <span class="size-tag">x10</span>
  </section>

  <section class="banner banner--dark" aria-label="Black Friday banner, dark version">
    <svg class="banner__art" viewBox="0 0 1500 480" preserveAspectRatio="none">
      <defs>
        <linearGradient id="bedroomPhoto" x1="0" y1="0" x2=".45" y2="1">
          <stop offset="0" stop-color="#e6e8e8"/>
          <stop offset=".22" stop-color="#d2c8bc"/>
          <stop offset=".4" stop-color="#c09066"/>
          <stop offset=".62" stop-color="#a77a55"/>
          <stop offset=".78" stop-color="#4a4e55"/>
          <stop offset=".9" stop-color="#5c5f63"/>
          <stop offset="1" stop-color="#cfc4b6"/>
        </linearGradient>
      </defs>
      <rect x="540" y="0" width="960" height="480" fill="url(#bedroomPhoto)" role="img" aria-label="Photo of a modern bedroom with a dark grey bed, wood panelled wall, pendant lamps and large window"/>
      <polygon points="0,0 515,0 738,480 0,480" fill="var(--black)"/>
      <polygon points="515,0 550,0 773,480 738,480" fill="var(--orange)"/>
      <rect x="226" y="309" width="600" height="128" fill="rgba(0,0,0,.35)"/>
      <rect x="218" y="302" width="600" height="128" fill="var(--orange)"/>
      <rect x="218" y="302" width="217" height="128" fill="var(--white)"/>
      <rect x="437" y="320" width="364" height="92" fill="var(--white)"/>
    </svg>

    <div class="title-block" style="left:-11px">
      <p class="line script" style="top:31px">The Big Black</p>
      <p class="line headline" style="top:58px">FRIDAY</p>
      <p class="line event" style="top:102px">EVENT</p>
      <p class="line tagline" style="top:185px">SALE MUST END SOON</p>
    </div>

    <p class="line promo-upto" style="left:169px;top:224px">UPTO</p>
    <p class="line promo-figure" style="left:168px;top:233px">70%</p>
    <p class="line promo-label" style="left:326px;top:247px">OFF EVERTHING</p>
    <span class="size-tag">x10</span>
  </section>

</main>
</body>
</html>
```